Refresh Velquor Web Presence - www.velquor-sample.com

Velquor (www.velquor-sample.com)web site needs a makeover. It needs to be more modern, less cluttered, more corporate, prestigious, user friendly, impressive, up to date. We want a modern corporate image that encourages our business users to trust us and buy our products and services. They need to understand that they are dealing with a highly reputable, long established company, but one that is up to date and forward thinking.
1. Clean uncluttered design.
2. Domain Registration box and Countries (price) box to be collapsible and expandable.
3. All links on page need to be conserved for SEO but hidden from view.
4. Logo and general colour scheme need to be retained.
5. Phone number to be prominently displayed at top of page.
6. No calls to action (CTA) below the fold.
7. Sites we like: www.brinzal-sample.com, www.tundexa-sample.com,www.qop.com,www.plavion-sample.com, www.fismet-sample.com (busy but clear CTAs), www.yarmel-sample.com
Reason: We lost a lot of time to review over the holiday weekend. We need to have a chance to interact during business hours.
Target Market(s)
Small business to large enterprise
Industry/Entity Type
Business
Look and feel

```html
<!DOCTYPE html>
<html lang="en">
<head>
<meta charset="utf-8">
<title>Velquor – Domain Names</title>
<link rel="stylesheet" href="https://fonts.googleapis.com/css2?family=Oswald:wght@400;500&family=Ubuntu:wght@300;400;500;700&display=swap">
<style>
:root{
  --navy:#2e3386;
  --navy-dark:#23286f;
  --bar-top:#3d43a0;
  --bar-bottom:#2a2f85;
  --orange:#ef7d1e;
  --orange-dark:#d9600f;
  --orange-text:#e2701c;
  --ink:#1c1c1c;
  --grey-text:#4a4a4a;
  --line:#cfcfcf;
  --hero-a:#f4f5e3;
  --hero-b:#fbfcf6;
  --white:#ffffff;
}
*{box-sizing:border-box;margin:0;padding:0}
html,body{width:1200px;height:1007px;overflow:hidden;background:var(--white)}
body{position:relative;font-family:"Ubuntu",sans-serif;color:var(--ink)}
.abs{position:absolute}

/* utility bar */
.utility-bar{left:0;top:0;width:1200px;height:41px;background:linear-gradient(var(--bar-top),var(--bar-bottom))}
.utility-bar .link{position:absolute;top:12px;color:var(--white);font-size:13.5px}
.chat-icon{left:94px;top:13px}
.whois{left:201px;top:10px;width:177px;height:21px;display:flex}
.whois-field{flex:1;background:var(--white);font-size:13px;color:#666;padding:3px 8px}
.whois-btn{width:26px;background:var(--orange);display:flex;align-items:center;justify-content:center}
.phone-icon{left:563px;top:11px}
.phone-number{left:577px;top:5px;font-family:"Oswald",sans-serif;font-size:21px;color:var(--white);letter-spacing:.2px}
.login{left:1002px;top:0;width:84px;height:41px;background:var(--orange);color:var(--white);font-size:15px;display:flex;align-items:center;padding-left:14px;gap:8px}

/* hero */
.hero{left:0;top:41px;width:1200px;height:494px;background:radial-gradient(ellipse at 35% 40%,var(--hero-b),var(--hero-a) 70%,#e9ecd0);border-bottom:1px solid #dcdccc;box-shadow:0 2px 3px rgba(0,0,0,.08)}
.brand{left:96px;top:76px;display:flex;align-items:center;gap:10px}
.brand-dot{width:40px;height:40px;border-radius:50%;background:var(--orange)}
.brand-name{font-size:40px;font-weight:700;color:var(--navy);letter-spacing:.5px}
.main-nav{left:369px;top:89px;display:flex;align-items:center;height:32px}
.main-nav a{font-size:16px;font-weight:700;color:var(--ink);text-decoration:none;margin-right:17px}
.main-nav a.current{position:relative;background:var(--orange);color:var(--white);padding:6px 8px 7px 11px;margin-right:7px}
.main-nav a.current::after{content:"";position:absolute;left:57px;bottom:-7px;border:7px solid transparent;border-bottom:0;border-top-color:var(--orange)}
.headline{left:96px;top:168px;font-family:"Oswald",sans-serif;color:var(--navy);line-height:1}
.headline .count{font-size:112px;font-weight:500;letter-spacing:-1px}
.headline .plus{font-size:60px;font-weight:500;vertical-align:28px}
.headline .word{font-size:80px;font-weight:400}
.headline .line2{display:block;font-size:78px;margin-top:-3px}
.tagline{left:97px;top:374px;font-size:32px;font-weight:300;color:var(--orange-text)}
.pricing-btn{left:100px;top:441px;width:284px;height:60px;border:2px solid var(--white);border-radius:5px;box-shadow:0 1px 4px rgba(0,0,0,.35);background:linear-gradient(var(--orange),var(--orange-dark));display:flex;align-items:center;justify-content:center;gap:24px;font-family:"Oswald",sans-serif;font-size:35px;color:var(--white)}
.hero-visual{left:680px;top:150px;width:410px;height:350px;border-radius:50%;background:radial-gradient(circle at 50% 45%,#f0a640 0,#f3c77e 28%,rgba(240,235,210,.4) 62%,rgba(240,240,220,0) 72%)}
.slider-dots{left:1021px;top:501px;display:flex;gap:3px}
.slider-dots span{width:18px;height:18px;border-radius:50%;border:2px solid var(--white);background:var(--navy);box-shadow:0 0 2px rgba(0,0,0,.3)}
.slider-dots span.on{background:var(--orange)}

/* search tabs */
.search-tabs{left:93px;top:585px;display:flex;height:42px;align-items:center}
.search-tabs a{font-size:19px;font-weight:500;color:var(--grey-text);text-decoration:none;margin-right:26px}
.search-tabs a.current{background:linear-gradient(#dedede,#fff);height:42px;line-height:42px;padding:0 13px;margin-right:13px;border-top:2px solid #ccc}
.country-btn{left:916px;top:587px;width:168px;height:34px;border-radius:5px;background:linear-gradient(var(--orange),var(--orange-dark));color:var(--white);font-size:16px;font-weight:500;display:flex;align-items:center;justify-content:center;gap:8px}
.www{left:93px;top:682px;font-size:33px;font-weight:700;color:var(--navy)}
.domain-field{left:200px;top:672px;width:640px;height:66px;border:3px solid var(--line);border-radius:5px;font-size:35px;font-weight:300;color:#a8a8a8;padding:11px 21px}
.search-btn{left:810px;top:672px;width:273px;height:66px;background:linear-gradient(#f6932e,var(--orange-dark));clip-path:polygon(20px 0,100% 0,100% 100%,20px 100%,0 50%);display:flex;align-items:center;justify-content:center;gap:20px;font-family:"Oswald",sans-serif;font-size:40px;color:var(--white);padding-left:18px}

/* extension picker */
.picker{left:94px;top:780px;width:990px;height:195px;border:2px solid var(--line);border-radius:5px;background:var(--white)}
.region-bar{left:0;top:0;width:986px;height:44px;background:var(--navy)}
.region-pointer{left:22px;top:44px;width:114px;height:13px;background:var(--navy);clip-path:polygon(0 0,100% 0,50% 100%)}
.region{position:absolute;top:11px;display:flex;align-items:center;gap:11px;font-size:17px;font-weight:700;color:var(--white)}
.box{width:20px;height:20px;border:2px solid #aaa;background:var(--white);position:relative}
.region .box{border-color:#777}
.box.checked svg{position:absolute;left:0;top:-7px}
.ext{position:absolute;display:flex;align-items:center;gap:10px;font-size:15px;color:#333}
.more-btn{left:491px;top:959px;width:199px;height:30px;border:2px solid var(--line);border-radius:15px;background:var(--white);color:var(--orange-text);font-size:14px;font-weight:700;display:flex;align-items:center;justify-content:center;gap:6px}
</style>
</head>
<body>

<header class="abs utility-bar">
  <svg class="abs chat-icon" width="14" height="13" viewBox="0 0 14 13"><path d="M7 1C3.5 1 1 3 1 5.5c0 1.4.8 2.6 2 3.4L2.5 12 6 9.9h1c3.5 0 6-2 6-4.4S10.5 1 7 1z" fill="#fff"/></svg>
  <span class="link" style="left:115px">Chat with us</span>
  <div class="abs whois">
    <span class="whois-field">Whois Seach</span>
    <span class="whois-btn"><svg width="13" height="13" viewBox="0 0 13 13"><circle cx="5" cy="5" r="3.5" fill="none" stroke="#fff" stroke-width="2"/><path d="M7.5 7.5l4 4" stroke="#fff" stroke-width="2.4"/></svg></span>
  </div>
  <svg class="abs phone-icon" width="9" height="17" viewBox="0 0 9 17"><rect x="1" y="3" width="7" height="13" rx="1.2" fill="#fff"/><rect x="2.5" y="0" width="1.5" height="4" fill="#fff"/><rect x="2.3" y="5" width="4.4" height="4" fill="var(--navy)"/></svg>
  <span class="abs phone-number">+1.5550148207</span>
  <span class="link" style="left:725px">Register</span>
  <span class="link" style="left:792px">Shopping Cart</span>
  <span class="link" style="left:903px">View Cart (0)</span>
  <div class="abs login">Login <svg width="14" height="9" viewBox="0 0 14 9"><path d="M0 0h14L7 9z" fill="#fff"/></svg></div>
</header>

<section class="abs hero">
</section>
<div class="abs brand"><span class="brand-dot"></span><span class="brand-name">velquor</span></div>
<nav class="abs main-nav">
  <a class="current" href="#">Domain Names</a>
  <a href="#">IDN Domains</a>
  <a href="#">New gTLDs</a>
  <a href="#">Phone Numbers</a>
  <a href="#">Hosting</a>
  <a href="#">Resellers</a>
  <a href="#">About Us</a>
</nav>
<h1 class="abs headline"><span class="count">300</span><span class="plus">+</span><span class="word"> Domain</span><span class="line2">Name Extensions</span></h1>
<p class="abs tagline">Accredited in over 100 countries</p>
<div class="abs pricing-btn">VIEW PRICING <svg width="26" height="28" viewBox="0 0 26 28"><path d="M0 0l13 14L0 28zM12 0l14 14-14 14z" fill="#fff"/></svg></div>
<div class="abs hero-visual" role="img" aria-label="Illustration of an open cardboard box surrounded by floating coloured domain extensions such as .com, .org, .net and .biz"></div>
<div class="abs slider-dots"><span class="on"></span><span></span><span></span></div>

<nav class="abs search-tabs">
  <a class="current" href="#">Domain Registration</a>
  <a href="#">IDN</a>
  <a href="#">Bulk Search</a>
  <a href="#">Transfer</a>
  <a href="#">Renew</a>
  <a href="#">Map Search</a>
  <a href="#">PhNUM</a>
</nav>
<div class="abs country-btn">Select Country <svg width="14" height="9" viewBox="0 0 14 9"><path d="M0 0h14L7 9z" fill="#fff"/></svg></div>

<span class="abs www">www.</span>
<div class="abs domain-field">Search for a new domain</div>
<div class="abs search-btn">SEARCH <svg width="34" height="36" viewBox="0 0 34 36"><circle cx="13" cy="13" r="10" fill="none" stroke="#fff" stroke-width="4"/><path d="M20 21l11 12" stroke="#fff" stroke-width="6" stroke-linecap="round"/></svg></div>

<section class="abs picker">
  <div class="abs region-bar"></div>
  <div class="abs region-pointer"></div>
  <label class="region" style="left:24px"><span class="box"></span>Generic</label>
  <label class="region" style="left:157px"><span class="box"></span>Europe</label>
  <label class="region" style="left:285px"><span class="box checked"><svg width="24" height="24" viewBox="0 0 24 24"><path d="M3 14l5 6L21 1" fill="none" stroke="var(--navy-dark)" stroke-width="3.5"/></svg></span>Asia/Pacific</label>
  <label class="region" style="left:449px"><span class="box"></span>America</label>
  <label class="region" style="left:586px"><span class="box"></span>Africa</label>
  <label class="region" style="left:718px"><span class="box"></span>All Domains</label>

  <label class="ext" style="left:34px;top:80px"><span class="box"></span>.biz</label>
  <label class="ext" style="left:141px;top:80px"><span class="box"></span>.co</label>
  <label class="ext" style="left:253px;top:80px"><span class="box checked"><svg width="24" height="24" viewBox="0 0 24 24"><path d="M3 14l5 6L21 1" fill="none" stroke="var(--navy-dark)" stroke-width="3.5"/></svg></span>.com</label>
  <label class="ext" style="left:366px;top:80px"><span class="box"></span>.info</label>
  <label class="ext" style="left:473px;top:80px"><span class="box"></span>.mobi</label>
  <label class="ext" style="left:584px;top:80px"><span class="box checked"><svg width="24" height="24" viewBox="0 0 24 24"><path d="M3 14l5 6L21 1" fill="none" stroke="var(--navy-dark)" stroke-width="3.5"/></svg></span>.name</label>
  <label class="ext" style="left:694px;top:80px"><span class="box"></span>.net</label>
  <label class="ext" style="left:778px;top:80px"><span class="box"></span>.me</label>
  <label class="ext" style="left:864px;top:80px"><span class="box"></span>.org</label>

  <label class="ext" style="left:34px;top:131px"><span class="box"></span>.pro</label>
  <label class="ext" style="left:141px;top:131px"><span class="box"></span>.pty-ltd.com</label>
  <label class="ext" style="left:253px;top:131px"><span class="box checked"><svg width="24" height="24" viewBox="0 0 24 24"><path d="M3 14l5 6L21 1" fill="none" stroke="var(--navy-dark)" stroke-width="3.5"/></svg></span>.tel</label>
  <label class="ext" style="left:366px;top:131px"><span class="box"></span>.travel</label>
  <label class="ext" style="left:473px;top:131px"><span class="box"></span>.xxx</label>
</section>
<div class="abs more-btn">Show More Extensions <svg width="14" height="12" viewBox="0 0 14 12"><path d="M0 0h14L7 8z M0 5h14L7 12z" fill="var(--orange)"/></svg></div>

</body>
</html>
```